Website Design Project for Beauty & Wellness Professionals

As background information, I have a website that is focused on Beauty & Wellness Professionals:
- Job Search (www.lumarinovo.com)
- Business Classifieds (negocios.lumarinovo.com)
- Freelancer Classifieds (freelancer.lumarinovo.com)
- Course Reviews (cursos.lumarinovo.com)

All those websites use standard templates.

I need a DESIGN for the HOME PAGE (no coding) of the Website Platform that consolidates the four platforms under the same design.

Website designs that we like:
- quelvox.com
- brintmoor.com

Target Market(s)

Brazilian Professionals from Beauty & Wellness sector

Industry/Entity Type

Business

Requirements
Must have
• Website designs that we like:
- quelvox.com
- brintmoor.com

```html
<!DOCTYPE html>
<html lang="pt">
<head>
<meta charset="utf-8">
<title>Lumarinovo – Home</title>
<link rel="stylesheet" href="https://fonts.googleapis.com/css2?family=PT+Sans:wght@400;700&display=swap">
<style>
:root{
  --topbar:#72c0d8;
  --teal:#3d98b8;
  --teal-dark:#3a8eaa;
  --footer-top:#58aec8;
  --footer-bottom:#3f93b0;
  --link:#3a8fc0;
  --text:#555;
  --muted:#888;
  --line:#dcdcdc;
  --panel:#f1f1f1;
  --orange:#e2741a;
  --orange-light:#f2922f;
  --green:#3f9a2c;
  --brand:#4aa3b8;
  --search:#4ea9cc;
}
*{box-sizing:border-box;margin:0;padding:0}
html,body{width:686px;height:1200px;overflow:hidden;background:#fff}
body{font-family:"PT Sans",sans-serif;color:var(--text);position:relative}
.abs{position:absolute}
a{color:inherit;text-decoration:none}

.topbar{left:0;top:0;width:686px;height:18px;background:var(--topbar);color:#fff;font-size:7.5px;text-align:right;padding:4px 60px 0 0}
.header{left:0;top:18px;width:686px;height:66px;background:linear-gradient(#fff 60%,#eef0f1)}
.brand{left:54px;top:36px;display:flex;align-items:center;gap:6px;color:var(--brand);font-size:20px}
.brand-mark{width:20px;height:20px;border-radius:50%;background:var(--brand)}
.social-mini{left:216px;top:48px;display:flex;gap:3px}
.social-mini span{width:15px;height:15px;background:#2f6fb3;border-radius:2px}
.social-mini span:nth-child(3){background:#3fa6dd}
.social-mini span:nth-child(4),.social-mini span:nth-child(5){background:#c9302c}
.nav{left:317px;top:49px;display:flex;font-size:11px;color:#333}
.nav a{padding:0 8px;border-left:1px solid #ccc;line-height:12px}
.nav a:first-child{border:0;padding-left:0}

.hero{left:0;top:84px;width:686px;height:257px;background:linear-gradient(100deg,#c9b9a2 0%,#e7dccb 35%,#d9cbb6 60%,#efe9e0 100%)}
.hero-window{left:0;top:84px;width:560px;height:90px;background:linear-gradient(90deg,#8fb85a,#b8d58a,#8db45c);opacity:.6}
.hero-title{left:101px;top:176px;color:#fff;text-shadow:0 1px 3px rgba(0,0,0,.35)}
.hero-title .small{font-size:18px;font-weight:700;display:block}
.hero-title .big{font-size:29px;font-weight:700;display:block;margin-top:4px}
.searchbar{left:101px;top:242px;width:485px;height:41px;background:rgba(40,40,40,.78);border-radius:2px}
.field{position:absolute;top:9px;height:21px;background:#fff;font-size:9px;color:#999;padding:5px 8px}
.field.select{left:8px;width:80px;color:#333;background:linear-gradient(#fff,#e6e6e6)}
.field.select::after{content:"";position:absolute;right:6px;top:8px;border:4px solid transparent;border-top:5px solid #444}
.field.select::before{content:"";position:absolute;right:18px;top:2px;bottom:2px;border-left:1px solid #bbb}
.field.key{left:93px;width:181px}
.field.loc{left:279px;width:125px}
.btn-search{position:absolute;left:410px;top:9px;width:64px;height:21px;background:linear-gradient(#6ec0e0,var(--search));color:#fff;font-size:10px;text-align:center;line-height:21px}

.tabs{left:175px;top:363px;display:flex;gap:4px}
.tab{height:26px;padding:0 8px;border:1px solid #ccc;border-bottom:0;background:#eee;font-size:9.5px;color:#444;line-height:26px}
.tab.active{background:#fff;height:27px}
.tabs-line{left:157px;top:389px;width:371px;border-top:1px solid #ccc}

.job{left:154px;width:344px;height:60px}
.job-logo{position:absolute;left:0;top:2px;width:48px;height:46px;border:1px solid #ddd;background:#fff;box-shadow:0 1px 2px rgba(0,0,0,.1)}
.job-logo i{position:absolute;left:9px;top:8px;width:28px;height:28px;border-radius:50%}
.job-title{position:absolute;left:60px;top:0;width:160px;font-size:9.5px;color:var(--link);line-height:12px}
.job-meta{position:absolute;left:60px;width:160px;font-size:6.6px;color:var(--muted);line-height:10px}
.job-loc{position:absolute;left:234px;top:0;width:60px;font-size:9.5px;color:#444}
.job-loc small{display:block;font-size:6.5px;color:var(--muted);line-height:10px;margin-top:2px}
.job-date{position:absolute;left:314px;top:0;font-size:9.5px;color:#444}
.job-date small{display:block;font-size:6.5px;color:var(--muted);margin-top:2px}
.sep{left:157px;width:341px;border-top:1px solid #e2e2e2}

.pager{left:218px;top:612px;width:256px;height:24px;background:#eee;display:flex;gap:4px;padding:4px 8px}
.pager span{height:15px;min-width:15px;padding:0 3px;background:#fff;border:1px solid #ddd;font-size:7.5px;line-height:13px;text-align:center;color:#333}
.pager .wide{width:34px}

.course-heading{left:118px;top:659px;font-size:12px;color:#222}
.course{width:131px}
.course-img{height:86px}
.course p{font-size:7.4px;line-height:12px;color:#777;margin-top:7px}
.btn-more{margin-top:6px;width:66px;height:19px;background:linear-gradient(var(--orange-light),var(--orange));color:#fff;font-size:7px;text-align:center;line-height:19px;border-radius:2px}

.divider{left:75px;top:852px;width:520px;border-top:1px solid #ddd}
.box{top:876px;width:154px;height:84px;background:var(--panel);padding:10px 14px}
.box h3{font-size:11.5px;font-weight:400}
.box .green{color:var(--green)}
.box .orange{color:var(--orange)}
.box .teal{color:var(--teal)}
.email{margin-top:6px;width:128px;height:14px;border:1px solid #ddd;background:#fff;font-size:6px;color:#777;padding:2px 5px}
.btn-sub{margin:6px 0 0 72px;width:56px;height:16px;background:linear-gradient(#5cb43c,var(--green));color:#fff;font-size:8px;text-align:center;line-height:16px;border-radius:2px}
.vacancy-list{display:grid;grid-template-columns:72px 72px;font-size:6.4px;color:#444;row-gap:5px;margin-top:7px}
.vacancy-list span::before{content:"› "}
.box3 p{font-size:6.5px;line-height:12px;color:#777;margin-top:3px}
.edu-badge{position:absolute;right:12px;bottom:9px;width:8px;height:8px;background:var(--orange)}

.footer{left:0;top:986px;width:686px;height:174px;background:linear-gradient(var(--footer-top),var(--footer-bottom));border-top:3px solid #8fd0e3}
.footer h4{position:absolute;font-size:12px;font-weight:400;color:#fff}
.feed{left:70px;top:1032px;width:175px;height:108px;background:#fff;padding:6px}
.feed-grid{display:grid;grid-template-columns:repeat(4,37px);gap:6px 7px}
.feed-grid div{height:38px;background:linear-gradient(#d8b49a,#b88e74)}
.feed small{display:block;font-size:5.5px;color:#999;margin-top:3px}
.follow{font-size:7px;color:#fff;display:flex;align-items:center;gap:7px}
.follow i{width:19px;height:19px;display:inline-block}

.bottombar{left:0;top:1160px;width:686px;height:40px;background:var(--teal-dark);color:#fff;font-size:7.5px;text-align:center;padding-top:14px}
</style>
</head>
<body>

<div class="abs topbar">Advertise Job Vacancy &nbsp;:&nbsp; Sign In &nbsp;|&nbsp; Register</div>

<header class="abs header"></header>
<div class="abs brand"><span class="brand-mark"></span>Lumarinovo</div>
<div class="abs social-mini" aria-label="Social links"><span></span><span></span><span></span><span></span><span></span></div>
<nav class="abs nav"><a>Blog</a><a>For Business</a><a>Events &amp; Partners</a><a>About Us</a><a>Contact</a></nav>

<div class="abs hero" role="img" aria-label="Photo of a mother with her baby using a laptop on a sofa"></div>
<div class="abs hero-window" aria-hidden="true"></div>
<div class="abs hero-title"><span class="small">Looking for a Career In Beauty..</span><span class="big">Find Your Dream Job</span></div>
<div class="abs searchbar">
  <div class="field select">Jobs</div>
  <div class="field key">Key tittle or company</div>
  <div class="field loc">Locations</div>
  <div class="btn-search">SEARCH</div>
</div>

<div class="abs tabs">
  <div class="tab active">Featured Job Vacancies</div>
  <div class="tab">Latest Job Vacancies</div>
  <div class="tab">Job Vacancies</div>
</div>
<div class="abs tabs-line"></div>

<div class="abs job" style="top:401px">
  <div class="job-logo"><i style="background:#b98f5e"></i></div>
  <div class="job-title">Aux. Hairdresser (Escovista) - Santo André (SP)</div>
  <div class="job-meta" style="top:26px">Marta Vieira / Ambra Hair and Esthetics - Posted by Marta De Vieira</div>
  <div class="job-loc">Santo André<small>São Paulo, the Federative Republic of Brazil</small></div>
  <div class="job-date">July 18<small>2013</small></div>
</div>
<div class="abs sep" style="top:462px"></div>
<div class="abs job" style="top:472px">
  <div class="job-logo"><i style="background:#3cc6c4;border-radius:0;left:4px;top:4px;width:38px;height:36px"></i></div>
  <div class="job-title">Manicure - Closest subway Vila Madalena - São Paulo (SP)</div>
  <div class="job-meta" style="top:26px">RJ Manicure and Waxing - Posted by jobs</div>
  <div class="job-loc">Santo André<small>São Paulo, the Federative Republic of Brazil</small></div>
  <div class="job-date">July 18<small>2013</small></div>
</div>
<div class="abs sep" style="top:530px"></div>
<div class="abs job" style="top:542px">
  <div class="job-logo"><i style="background:#2c3f86"></i></div>
  <div class="job-title">Manicure - Jabalpur - São Paulo (SP)</div>
  <div class="job-meta" style="top:14px">Esmalteria Solaris - Unit Jabalpur - Posted by nina_carvalho</div>
  <div class="job-loc">Santo André<small>São Paulo, the Federative Republic of Brazil</small></div>
  <div class="job-date">July 18<small>2013</small></div>
</div>
<div class="abs sep" style="top:603px;width:371px"></div>

<div class="abs pager">
  <span class="wide">Prev</span><span>1</span><span>2</span><span>3</span><span>4</span><span>5</span><span>6</span><span>...</span><span>22</span><span class="wide">Next</span>
</div>

<h2 class="abs course-heading" style="font-weight:400">Online Course Lernavo</h2>
<div class="abs course" style="left:118px;top:682px">
  <div class="course-img" role="img" aria-label="Photo of a woman in pink working on a laptop" style="background:linear-gradient(135deg,#f3eef0,#e2cfd6)"></div>
  <p>Mauris vel lacus vitae felis vestibulum volutpat. Etiam est nunc venenatis</p>
  <div class="btn-more">READ MORE</div>
</div>
<div class="abs course" style="left:273px;top:682px">
  <div class="course-img" role="img" aria-label="Photo of a smiling woman in green at a desk with a laptop" style="background:linear-gradient(135deg,#f1f2f0,#cfd9c2)"></div>
  <p>Mauris vel lacus vitae felis vestibulum volutpat. Etiam est nunc venenatis</p>
  <div class="btn-more">READ MORE</div>
</div>
<div class="abs course" style="left:428px;top:682px">
  <div class="course-img" role="img" aria-label="Photo of two smiling young women together" style="background:linear-gradient(135deg,#c9a58a,#ecd9c8)"></div>
  <p>Mauris vel lacus vitae felis vestibulum volutpat. Etiam est nunc venenatis</p>
  <div class="btn-more">READ MORE</div>
</div>

<div class="abs divider"></div>

<div class="abs box" style="left:94px">
  <h3 class="green">Assinar Por Email</h3>
  <div class="email">email address</div>
  <div class="btn-sub">Subscribe</div>
</div>
<div class="abs box" style="left:262px">
  <h3 class="orange">Job Vacancy</h3>
  <div class="vacancy-list">
    <span>Assistant Hairdresser</span><span>Designer Eyebrow</span>
    <span>Assistant Cleaning</span><span>Featured</span>
    <span>Hairdresser</span><span>Nurse</span>
  </div>
</div>
<div class="abs box box3" style="left:431px">
  <h3 class="teal">Online Courses Lernavo</h3>
  <p>Nunc tempus felis vitae urna. Vivamus porttitor, g, purus nisi eleifend libero, a tempus libero lectus feugiat felis.</p>
  <span class="edu-badge"></span>
</div>

<footer class="abs footer">
  <h4 style="left:70px;top:27px">Friendwall Feed</h4>
  <h4 style="left:284px;top:27px">Follow Us</h4>
</footer>
<div class="abs feed">
  <div class="feed-grid" role="img" aria-label="Grid of member profile photos">
    <div></div><div style="background:linear-gradient(#e8ddd6,#c8b2a4)"></div><div style="background:linear-gradient(#c98a68,#a8684d)"></div><div style="background:linear-gradient(#9b7a5a,#6f5540)"></div>
    <div style="background:linear-gradient(#7a5a48,#503a2e)"></div><div style="background:linear-gradient(#e0b68e,#c2936d)"></div><div style="background:linear-gradient(#d3ab8c,#a78067)"></div><div style="background:linear-gradient(#efe4da,#d8c3b3)"></div>
  </div>
  <small>friendwall page</small>
</div>
<div class="abs follow" style="left:286px;top:1032px"><i style="background:#3aa6de"></i>On Chirpline</div>
<div class="abs follow" style="left:286px;top:1057px"><i style="background:#e38a2d"></i>As RSS Feed</div>
<div class="abs follow" style="left:286px;top:1082px"><i style="background:#3b5a98"></i>Shared on Friendwall</div>
<div class="abs follow" style="left:286px;top:1105px"><i style="background:#444"></i>On Orbitplus</div>
<div class="abs follow" style="left:394px;top:1032px"><i style="background:#c8232c"></i>Pinboardly</div>
<div class="abs follow" style="left:394px;top:1057px"><i style="background:#cc3030"></i>Vidtube</div>
<div class="abs follow" style="left:394px;top:1082px"><i style="background:#2a6aa0"></i>Netlinkr</div>
<div class="abs follow" style="left:394px;top:1109px"><i style="background:#6a8db1"></i>Snapgram</div>

<div class="abs bottombar">© 2013 www.lumarinovo.com &nbsp;|&nbsp; Term and Conditions &nbsp;|&nbsp; Privacy Statement &nbsp;|&nbsp; Imprint &nbsp;|&nbsp; Glossary</div>

</body>
</html>
```